Design Book Cover for PhD Thesis on Cryptanalysis

I need a book cover design (front, back & spine) for my PhD thesis called "Studies on Lattice Sieves and Their Limits".
Author: Joris Kalden
Keywords: cryptanalysis, digital fingerprint, digital signature, digital certificate, collision of fingerprint/signature, bit-difference.
The finished book will have dimensions 17cm by 24cm by ?cm.
The (flat-)spine thickness is yet unknown, but will probably be about 1cm.
The cover design thus needs from left-to-right:
- a back of 17cm by 24cm
- in between a spine of about 1cm by 24cm
- a front of 17cm by 24cm
Around this design a 3mm bleeding/cutoff edge is needed
(leading to a total height of 24.6 cm and total width of 35.6cm).
The spine-fold is located 7mm from the spine on the front and back cover,
so the title etc. should be removed at least 1cm from the spine.
Below I will provide a description of my biggest results in my thesis and try to give some idea of the techniques used, which may help you for inspiration.
As you will read below, cryptanalysis comes close to "hacking".
However, cryptanalysis involves much more mathematics, and our goal is to provide recommendations which cryptographic standards are (un)safe to use.
So I would prefer a cover design that generally "feels" more as cryptanalysis than "hacking".
The biggest result in my thesis is the following.
Secure websites are secured using digital certificates.
These digital certificates contain the web domain name and the server's public-key and are digitally signed by a Certificate Authority (a company/government that only signs if the public-key really belongs to the owner of the web domain).
Only a few hundred Certification Authorities are trusted in web browsers and these are publically available.
Any digital certificate signed by such a Certification Authority is considered legitimate.
To fake a secure website you thus have to get a certificate containing your public-key in combination with the target domain name signed by a Certification Authority.
Our team was able to construct a rogue sub-Certification Authority, i.e.,
a Certification Authority that is authorized by one of the publicly known Certification Authorities.
Using our rogue Certification Authority we can thus create digital certificates at will for any secure website containing our public-key.
More detailed information is available at
http://www.cs.brelvor.nl/lattforge/false-root/
An idea of the techniques in my thesis:
I look at the internal computation of a digital signature for a certificate at bit-level and compare two such computations.
A difference between two certificates will lead to differences between the two internal computations of their digital signatures and finally to two different signatures.
However, we actively adapt the certificates to control the flow of these internal differences until we find two different certificates that actually result in the same digital signature, this is called a _collision_.
Evidently, my thesis is very technical and I have tried here to provide a short description.
You can always contact me for questions and/or more detailed explanations.
Reason: Almost all designs focus on the very general topic of digital security (digital fingerprint, etc).
I am looking more for a design that reflects more on the topic of the thesis: attacks on hash functions.
Several ideas have already been given in the brief and discussion.
Since the old deadline is already tomorrow, I am extend it.

```html
<!DOCTYPE html>
<html lang="en">
<head>
<meta charset="utf-8">
<title>Studies on Lattice Sieves and Their Limits — Book Cover</title>
<link rel="stylesheet" href="https://fonts.googleapis.com/css2?family=Share+Tech+Mono&display=swap">
<style>
  :root {
    --paper: #ffffff;
    --frame: #1a1a1a;
    --spine-red: #e41e26;
    --title-red: #e8202a;
    --ink: #0d0d0d;
    --sky-light: #5fd0f5;
    --sky-mid: #25a8e6;
    --sky-deep: #1378c4;
    --print-faint: #d6ecf7;
    --print-black: #111111;
    --spine-text: #ffffff;
  }
  * { margin: 0; padding: 0; box-sizing: border-box; }
  html, body {
    width: 1200px; height: 826px;
    overflow: hidden;
    background: var(--paper);
  }
  .cover {
    position: relative;
    width: 1200px; height: 826px;
    font-family: "Share Tech Mono", "Courier New", monospace;
  }
  .back-cover {
    position: absolute;
    left: 14px; top: 12px;
    width: 571px; height: 804px;
    background: var(--paper);
    border: 1px solid var(--frame);
    overflow: hidden;
  }
  .back-fingerprint {
    position: absolute;
    left: 0; top: 0;
    width: 571px; height: 804px;
  }
  .spine {
    position: absolute;
    left: 585px; top: 12px;
    width: 33px; height: 804px;
    background: var(--spine-red);
  }
  .spine-title, .spine-author {
    position: absolute;
    left: 50%;
    color: var(--spine-text);
    white-space: nowrap;
    transform-origin: 0 0;
  }
  .spine-title {
    top: 36px;
    font-size: 21px;
    letter-spacing: 0.5px;
    transform: rotate(90deg) translateY(-50%);
  }
  .spine-author {
    top: 650px;
    font-size: 13px;
    transform: rotate(90deg) translateY(-50%);
  }
  .front-cover {
    position: absolute;
    left: 618px; top: 12px;
    width: 569px; height: 804px;
    overflow: hidden;
    background: radial-gradient(ellipse 70% 55% at 50% 52%, var(--sky-light) 0%, var(--sky-mid) 45%, var(--sky-deep) 100%);
  }
  .front-fingerprint {
    position: absolute;
    left: 0; top: 0;
    width: 569px; height: 804px;
  }
  .front-title {
    position: absolute;
    left: 0; right: 0;
    top: 62px;
    text-align: center;
    font-size: 44px;
    line-height: 52px;
    font-weight: 400;
    color: var(--ink);
  }
  .front-title .title-lead { color: var(--title-red); display: block; }
  .front-title .title-line { display: block; }
  .front-author {
    position: absolute;
    left: 0; right: 0;
    top: 693px;
    text-align: center;
    font-size: 18px;
    color: var(--ink);
  }
</style>
</head>
<body>
<main class="cover">
  <section class="back-cover">
    <svg class="back-fingerprint" viewBox="0 0 571 804" role="img" aria-label="Large faint light-blue fingerprint illustration split by a diagonal seam">
      <ellipse cx="262" cy="420" rx="235" ry="300" transform="rotate(28 262 420)" fill="var(--print-faint)"/>
    </svg>
  </section>

  <section class="spine">
    <span class="spine-title">STUDIES ON LATTICE SIEVES AND THEIR LIMITS</span>
    <span class="spine-author">Author: Joris Kalden</span>
  </section>

  <section class="front-cover">
    <svg class="front-fingerprint" viewBox="0 0 569 804" role="img" aria-label="Fingerprint illustration split diagonally, upper half red and lower half black, over light streaks">
      <defs>
        <linearGradient id="print-split" x1="0" y1="0" x2="1" y2="1">
          <stop offset="0" stop-color="var(--title-red)"/>
          <stop offset="0.48" stop-color="var(--title-red)"/>
          <stop offset="0.56" stop-color="var(--print-black)"/>
          <stop offset="1" stop-color="var(--print-black)"/>
        </linearGradient>
      </defs>
      <ellipse cx="282" cy="455" rx="150" ry="172" transform="rotate(30 282 455)" fill="url(#print-split)"/>
    </svg>
    <h1 class="front-title">
      <span class="title-lead">STUDIES ON</span>
      <span class="title-line">LATTICE SIEVES AND</span>
      <span class="title-line">THEIR LIMITS</span>
    </h1>
    <p class="front-author">Author: Joris Kalden</p>
  </section>
</main>
</body>
</html>
```